Computer consultant business card

Bexil Software is a newly started computer consulting company. It's a small one-man company that provides mostly Vornix applications but also websites in collaboration with designers. I'm running this company on the side of full time university studies.

I want the final design to be clean and memorable. Be creative! :)

Some inspiration:
http://www.pixelmarta.com/design/48317
http://www.pixelmarta.com/design/2739164/business-card-design-by-frostlynk
http://www.pixelmarta.com/design/604281/business-card-design-by-koralind-vestrabanu

See attachment for my company logo.
Updates

I would like to thank everyone for submitting! I'll need a couple of days to review and ultimately select a design.

Target Market(s)

Non-technical entrepreneurs and small companies.

Industry/Entity Type

University

Requirements
Must have
• My company logo.
In any way, both colors from my logo.
First- and last name, e-mail and phone number.
Double-sided design.
Nice to have
• Something creative with the symbol in my logo

```html
<!DOCTYPE html>
<html lang="en">
<head>
<meta charset="utf-8">
<title>Bexil Software – Business Card Set</title>
<link href="https://fonts.googleapis.com/css2?family=Mulish:wght@400;700&display=swap" rel="stylesheet">
<style>
  :root {
    --backdrop: #b99b74;
    --label: #1e1a16;
    --paper: #ffffff;
    --charcoal: #353335;
    --ink: #333133;
    --brand-blue: #4471bd;
    --night: #050505;
    --slate-top: #2e2f35;
    --slate-bottom: #4b5877;
    --text-light: #ffffff;
    --text-muted: #d9d9d9;
  }
  * { margin: 0; padding: 0; box-sizing: border-box; }
  html, body {
    width: 1200px;
    height: 788px;
    overflow: hidden;
  }
  body {
    position: relative;
    background: var(--backdrop);
    font-family: "Mulish", "Helvetica Neue", Arial, sans-serif;
  }
  .side-label {
    position: absolute;
    width: 200px;
    text-align: center;
    font-size: 20px;
    color: var(--label);
  }
  .card {
    position: absolute;
    width: 525px;
    height: 299px;
    border-radius: 20px;
    overflow: hidden;
    box-shadow: 0 2px 6px rgba(0,0,0,0.35);
  }
  .card--front  { left: 55px;  top: 75px;  background: var(--paper); }
  .card--back-1 { left: 622px; top: 75px;  background: var(--paper); }
  .card--back-2 { left: 53px;  top: 446px; background: var(--night); }
  .card--back-3 {
    left: 622px; top: 446px;
    background: radial-gradient(ellipse 120% 110% at 85% 100%, var(--slate-bottom) 0%, #3c4356 45%, var(--slate-top) 100%);
  }
  .texture {
    position: absolute;
    inset: 0;
    background:
      radial-gradient(ellipse 40% 45% at 18% 5%, rgba(120,120,120,0.45), transparent 70%),
      radial-gradient(ellipse 30% 40% at 82% 92%, rgba(150,140,140,0.45), transparent 70%);
  }
  .brand {
    position: absolute;
    display: flex;
    align-items: center;
    gap: 20px;
  }
  .brand__dot {
    width: 84px;
    height: 84px;
    border-radius: 50%;
    background: var(--brand-blue);
    flex: none;
  }
  .brand__name {
    font-weight: 700;
    font-size: 86px;
    line-height: 1;
    letter-spacing: 1px;
    color: var(--ink);
    padding-bottom: 10px;
  }
  .brand--on-dark .brand__name { color: var(--text-light); }
  .card--front .brand { left: 118px; top: 36px; }
  .card--front .brand__dot { width: 80px; height: 80px; }
  .card--front .brand__name { font-size: 78px; }
  .card--back-1 .brand { left: 104px; top: 96px; }
  .card--back-2 .brand { left: 106px; top: 107px; }
  .card--back-3 .brand { left: 98px; top: 97px; }
  .web {
    position: absolute;
    left: 0; right: 0;
    text-align: center;
    font-size: 18px;
    letter-spacing: 3.5px;
    color: var(--ink);
  }
  .card--back-1 .web { top: 249px; }
  .card--back-2 .web, .card--back-3 .web { top: 256px; color: var(--text-light); }
  .wave { position: absolute; inset: 0; }
  .holder {
    position: absolute;
    left: 42px;
    top: 227px;
    color: var(--text-light);
  }
  .holder__name { font-size: 17px; font-weight: 700; }
  .holder__role { font-size: 12.5px; color: var(--text-muted); margin-top: 2px; }
  .divider {
    position: absolute;
    left: 262px;
    top: 225px;
    width: 1px;
    height: 53px;
    background: #8a888a;
  }
  .contact {
    position: absolute;
    left: 281px;
    top: 231px;
    font-size: 15px;
    line-height: 24px;
    color: var(--text-light);
  }
  .contact b { font-style: italic; }
</style>
</head>
<body>
  <div class="side-label" style="left:220px; top:34px;">Front</div>
  <div class="side-label" style="left:796px; top:34px;">Back - 1</div>
  <div class="side-label" style="left:224px; top:405px;">Back - 2</div>
  <div class="side-label" style="left:796px; top:405px;">Back - 3</div>

  <section class="card card--front" aria-label="Card front">
    <div class="brand">
      <span class="brand__dot"></span>
      <span class="brand__name">bexil</span>
    </div>
    <svg class="wave" viewBox="0 0 525 299" aria-hidden="true">
      <path d="M0 192 C60 168 110 160 170 171 C240 186 280 207 330 207 C400 207 470 184 525 166 L525 299 L0 299 Z" fill="var(--charcoal)"/>
      <path d="M110 160 C180 157 250 186 330 194 C410 199 470 178 525 158 L525 165 C470 186 410 205 330 201 C250 194 180 165 110 160 Z" fill="var(--brand-blue)"/>
    </svg>
    <div class="holder">
      <p class="holder__name">First Name Last Name</p>
      <p class="holder__role">Designation</p>
    </div>
    <div class="divider"></div>
    <div class="contact">
      <p><b>p</b> : +12 345 6789</p>
      <p><b>e</b> : info@website.com</p>
    </div>
  </section>

  <section class="card card--back-1" aria-label="Card back, white version">
    <div class="brand">
      <span class="brand__dot"></span>
      <span class="brand__name">bexil</span>
    </div>
    <p class="web">www.website.com</p>
  </section>

  <section class="card card--back-2" aria-label="Card back, black version">
    <div class="texture" role="img" aria-label="Perforated metal dot texture in soft grey highlights"></div>
    <div class="brand brand--on-dark">
      <span class="brand__dot"></span>
      <span class="brand__name">bexil</span>
    </div>
    <p class="web">www.website.com</p>
  </section>

  <section class="card card--back-3" aria-label="Card back, slate version">
    <div class="brand brand--on-dark">
      <span class="brand__dot"></span>
      <span class="brand__name">bexil</span>
    </div>
    <p class="web">www.website.com</p>
  </section>
</body>
</html>
```